TA BRAMLEY BUSINESS CARD DESIGN PROJECT

We need to utilize our logo that was expertly created on PixelHarbor and now need to match this with a business card design.

```html
<!DOCTYPE html>
<html lang="en">
<head>
<meta charset="utf-8">
<title>TA BRAMLEY Business Card</title>
<link rel="stylesheet" href="https://fonts.googleapis.com/css2?family=Montserrat:wght@400;500;700&display=swap">
<style>
  :root {
    --brand-blue: #1358b4;
    --brand-blue-dark: #0f4c9e;
    --card-white: #ffffff;
    --text-gray: #3a3a3a;
    --stage: #e9ebee;
  }
  * { margin: 0; padding: 0; box-sizing: border-box; }
  html, body {
    width: 1200px; height: 834px; overflow: hidden;
    background: var(--stage);
    font-family: "Montserrat", Arial, sans-serif;
  }
  .stage {
    width: 1200px; height: 834px;
    display: flex; align-items: center; justify-content: center; gap: 60px;
  }
  .card {
    position: relative;
    width: 520px; height: 298px;
    border-radius: 4px;
    overflow: hidden;
    box-shadow: 0 10px 28px rgba(0,0,0,0.18);
  }
  .card-front { background: var(--card-white); }
  .card-back { background: var(--brand-blue); }

  .holder { position: absolute; left: 34px; top: 30px; }
  .holder-name {
    font-weight: 700; font-size: 22px; color: var(--brand-blue);
    letter-spacing: 0.5px;
  }
  .holder-role { font-size: 13px; color: var(--text-gray); margin-top: 2px; }

  .divider {
    position: absolute; left: 34px; right: 34px; top: 96px;
    height: 1px; background: var(--brand-blue);
  }

  .contacts { position: absolute; left: 34px; top: 108px; list-style: none; }
  .contacts li {
    display: flex; align-items: center; gap: 8px;
    font-size: 13px; color: var(--text-gray); line-height: 22px;
  }
  .contacts svg { width: 12px; height: 12px; fill: var(--brand-blue); }

  .brand {
    position: absolute; right: 34px; top: 40px;
    display: flex; align-items: center; gap: 10px;
  }
  .brand-mark { width: 22px; height: 22px; background: var(--brand-blue); }
  .brand-name {
    font-weight: 700; font-size: 26px; color: var(--brand-blue);
    letter-spacing: 5px;
  }

  .address {
    position: absolute; right: 34px; top: 150px;
    text-align: right; font-size: 14px; color: var(--text-gray); line-height: 20px;
  }

  .band { position: absolute; left: 0; bottom: 0; width: 520px; height: 80px; }
  .website {
    position: absolute; right: 34px; bottom: 10px;
    font-size: 14px; color: var(--card-white); letter-spacing: 0.3px;
  }
  .back-pattern { position: absolute; inset: 0; background: linear-gradient(135deg, #1660c0, #0f4c9e); }
</style>
</head>
<body>
<main class="stage">
  <section class="card card-front">
    <div class="holder">
      <p class="holder-name">COLIN MARSH</p>
      <p class="holder-role">Managing Director</p>
    </div>

    <div class="brand">
      <span class="brand-mark"></span>
      <span class="brand-name">TA BRAMLEY</span>
    </div>

    <div class="divider"></div>

    <ul class="contacts">
      <li><svg viewBox="0 0 24 24"><path d="M6.6 10.8a15 15 0 0 0 6.6 6.6l2.2-2.2a1 1 0 0 1 1-.25 11.4 11.4 0 0 0 3.6.57 1 1 0 0 1 1 1V20a1 1 0 0 1-1 1A17 17 0 0 1 3 4a1 1 0 0 1 1-1h3.5a1 1 0 0 1 1 1c0 1.25.2 2.45.57 3.57a1 1 0 0 1-.25 1z"/></svg>123 456 789</li>
      <li><svg viewBox="0 0 24 24"><rect x="4" y="4" width="16" height="17" rx="2"/><rect x="7" y="1" width="10" height="4" rx="1"/></svg>123 456 789</li>
      <li><svg viewBox="0 0 24 24"><path d="M2 5h20v14H2z M2 5l10 8 10-8"/></svg>info@yourmail.com</li>
    </ul>

    <p class="address">Your address, City<br>State, Zip 1234</p>

    <svg class="band" viewBox="0 0 520 80" preserveAspectRatio="none" aria-hidden="true">
      <path d="M0 6 H220 L232 14 H0 Z" fill="#1358b4"/>
      <path d="M0 22 H236 Q252 22 268 38 H520 V80 H0 Z" fill="#1358b4"/>
    </svg>
    <p class="website">www.yourwebsite.com</p>
  </section>

  <section class="card card-back">
    <div class="back-pattern" role="img" aria-label="Repeating brand symbol pattern in tonal blue"></div>
  </section>
</main>
</body>
</html>
```